Brell Stone Company Business Cards

Front and Back Business Card - logo and text setup - cool design. I need workable photoshop or illustrator files so I can setup each employee card with design that is created
Updates

Hi everyone, thank you for the great entries. Please no more white and blue cards - there are so many already - black and silver only now please. thanks!

Target Market(s)

Construction Industry - Facility Managers

Industry/Entity Type

Construction

Contact Information for Business Card

I really like contemporary simplistic looks - clean neat....not opposed to seeing some black backrounds

Requirements
Must have
• Logo/website address with design on front only - www.brellstone-example.com (logo attached)
• Back:
• Name/Title/Company Address/Phone/email address
Nice to have
• Cool design
Should not have
• Nothing gimmicky like Fire or Water - since we are a Fire Protection company - it has all been done

```html
<!DOCTYPE html>
<html lang="en">
<head>
<meta charset="utf-8">
<title>Brell Stone Company Business Cards</title>
<link rel="stylesheet" href="https://fonts.googleapis.com/css2?family=Lato:wght@400;700;900&display=swap">
<style>
  :root {
    --backdrop: #3b3b3b;
    --black: #161618;
    --black-light: #45474b;
    --silver: #9ea3a9;
    --silver-light: #d9dbde;
    --paper: #e8e9eb;
    --ink: #55575a;
  }
  html, body {
    margin: 0;
    padding: 0;
    width: 1200px;
    height: 829px;
    overflow: hidden;
    background: var(--backdrop);
    font-family: "Lato", sans-serif;
  }
  .canvas {
    position: relative;
    width: 1200px;
    height: 829px;
  }
  .card {
    position: absolute;
    top: 282px;
    width: 485px;
    height: 278px;
    overflow: hidden;
    box-shadow: 0 3px 10px rgba(0,0,0,0.5);
  }
  /* Front */
  .card-front {
    left: 82px;
    background: radial-gradient(ellipse 200px 170px at 245px 160px, var(--black-light), var(--black));
  }
  .front-name {
    position: absolute;
    left: 0;
    right: 0;
    top: 112px;
    text-align: center;
    color: var(--silver-light);
    font-weight: 900;
    font-size: 42px;
    letter-spacing: -0.5px;
  }
  .front-web {
    position: absolute;
    left: 0;
    right: 0;
    top: 234px;
    text-align: center;
    color: var(--silver-light);
    font-size: 10.5px;
    letter-spacing: 1.2px;
  }
  /* Back */
  .card-back {
    left: 628px;
    background: var(--paper);
  }
  .card-back .swoosh {
    position: absolute;
    left: 0;
    top: 0;
  }
  .person {
    position: absolute;
    left: 36px;
    top: 114px;
  }
  .person-name {
    font-size: 15px;
    font-weight: 700;
    color: var(--black);
    line-height: 18px;
  }
  .person-name .surname { color: var(--silver); }
  .person-title {
    font-size: 11.5px;
    color: var(--ink);
    line-height: 14px;
  }
  .divider {
    position: absolute;
    left: 36px;
    top: 160px;
    width: 17px;
    height: 1px;
    background: var(--ink);
  }
  .contact {
    position: absolute;
    left: 36px;
    top: 177px;
    font-size: 11.5px;
    line-height: 14px;
    color: var(--ink);
  }
  .contact .address { margin-bottom: 6px; }
  .contact .row {
    display: flex;
    align-items: center;
    gap: 5px;
  }
  .contact svg { width: 9px; height: 9px; }
  .back-name {
    position: absolute;
    right: 36px;
    top: 200px;
    display: flex;
    align-items: center;
    gap: 7px;
    font-weight: 900;
    font-size: 24px;
    color: var(--black);
  }
  .back-name .mark {
    width: 10px;
    height: 10px;
    background: var(--silver);
  }
</style>
</head>
<body>
<div class="canvas">
  <section class="card card-front">
    <div class="front-name">Brell Stone</div>
    <div class="front-web">www.<b>brellstone-example</b>.com</div>
  </section>

  <section class="card card-back">
    <svg class="swoosh" width="485" height="278" viewBox="0 0 485 278">
      <rect width="485" height="278" fill="var(--black)"/>
      <path d="M0 53 Q230 -48 485 68 L485 278 L0 278 Z" fill="var(--paper)"/>
      <path d="M90 14 Q300 -4 485 76 L485 92 Q300 4 90 14 Z" fill="var(--silver)"/>
    </svg>
    <div class="person">
      <div class="person-name">Daniel <span class="surname">Marsh</span></div>
      <div class="person-title">Managing Director</div>
    </div>
    <div class="divider"></div>
    <div class="contact">
      <div class="address">Co. Street, Suite, Building<br>City/State, Zip Code</div>
      <div class="row">
        <svg viewBox="0 0 10 10"><path d="M2 1 L4 1 L4.6 3.2 L3.4 4 Q4.2 5.8 6 6.6 L6.8 5.4 L9 6 L9 8 Q9 9 8 9 Q1 8.5 1 2 Q1 1 2 1 Z" fill="var(--black)"/></svg>
        <span>300.555.0142</span>
      </div>
      <div class="row">
        <svg viewBox="0 0 10 10"><rect x="0.8" y="2" width="8.4" height="6" fill="none" stroke="var(--black)" stroke-width="1"/><path d="M0.8 2 L5 5.4 L9.2 2" fill="none" stroke="var(--black)" stroke-width="1"/></svg>
        <span>info@brellstone-example.com</span>
      </div>
    </div>
    <div class="back-name"><span class="mark"></span>Brell Stone</div>
  </section>
</div>
</body>
</html>
```